Velmora Battery Saver App UI design.

We need a mockup layout design of an Velmora app uncoded. This simple battery saver app is composed primarily by three screens described in the attached specification. After the mockup approved we need the UI elements sliced, the app icon and a banner for the nook mart.

```html
<!DOCTYPE html>
<html lang="en">
<head>
<meta charset="utf-8">
<title>Velmora Power Saver – History</title>
<link rel="stylesheet" href="https://fonts.googleapis.com/css2?family=Raleway:wght@400;500;600&family=Open+Sans:wght@400;600;700&display=swap">
<style>
  :root {
    --status-green: #1f9e57;
    --bar-green: #2dbe6c;
    --accent-green: #2ecc71;
    --unplug-blue: #1f9cc0;
    --tab-blue: #1b8fb8;
    --list-bg: #151515;
    --card-bg: #1d1d1d;
    --card-edge: #2e2e2e;
    --text-light: #ffffff;
    --text-soft: #e6e6e6;
    --nav-bg: #000000;
  }
  * { margin: 0; padding: 0; box-sizing: border-box; }
  html, body { width: 675px; height: 1200px; overflow: hidden; background: var(--list-bg); }
  body { position: relative; font-family: "Open Sans", Arial, sans-serif; color: var(--text-light); }

  .status-bar { position: absolute; top: 0; left: 0; width: 675px; height: 32px; background: var(--status-green); }
  .status-icons { position: absolute; right: 14px; top: 4px; display: flex; align-items: center; gap: 8px; }
  .status-time { font-family: "Roboto", "Open Sans", sans-serif; font-size: 25px; color: var(--text-light); line-height: 24px; }

  .app-bar { position: absolute; top: 32px; left: 0; width: 675px; height: 104px; background: var(--bar-green); box-shadow: 0 2px 3px rgba(0,0,0,.25); }
  .app-mark { position: absolute; left: 29px; top: 31px; width: 43px; height: 43px; background: var(--text-light); border-radius: 4px; }
  .app-title { position: absolute; left: 91px; top: 34px; font-family: "Open Sans", sans-serif; font-size: 30px; font-weight: 400; color: var(--text-light); }

  .tabs { position: absolute; top: 136px; left: 0; width: 675px; height: 71px; background: var(--text-light); overflow: hidden; }
  .tab { position: absolute; top: 22px; font-family: "Open Sans", sans-serif; font-size: 25px; letter-spacing: .5px; }
  .tab-history { left: 232px; width: 210px; text-align: center; color: var(--accent-green); }
  .tab-current { left: 552px; color: var(--tab-blue); }
  .tab-indicator { position: absolute; left: 232px; bottom: 0; width: 210px; height: 5px; background: var(--accent-green); }

  .log-count { position: absolute; top: 207px; left: 0; width: 675px; height: 80px; background: var(--accent-green);
    text-align: center; line-height: 80px; font-size: 25px; color: var(--text-light); }
  .log-count strong { font-weight: 700; }

  .log-card { position: absolute; left: 4px; width: 666px; height: 160px; background: var(--card-bg);
    border: 2px solid var(--card-edge); border-radius: 5px; overflow: hidden; }
  .log-card .edge { position: absolute; left: 0; top: 0; width: 20px; height: 100%; }
  .log-card.unplugged .edge { color: var(--unplug-blue); }
  .log-card.charging .edge { color: var(--accent-green); }
  .event { position: absolute; left: 64px; font-family: "Raleway", sans-serif; font-weight: 500; font-size: 30px; letter-spacing: .3px; }
  .level { position: absolute; right: 62px; font-family: "Open Sans", sans-serif; font-weight: 700; font-size: 27px; }
  .unplugged .event, .unplugged .level { color: var(--unplug-blue); }
  .charging .event, .charging .level { color: var(--accent-green); }
  .duration { position: absolute; left: 66px; top: 52px; font-size: 21px; color: var(--text-soft); }
  .stamp { position: absolute; font-size: 23px; font-weight: 700; color: var(--text-light); }
  .stamp.date { left: 67px; }
  .stamp.time { left: 245px; }
  .stamp.reading { right: 62px; }

  .unplugged .event, .unplugged .level { top: 14px; }
  .unplugged .stamp { top: 104px; }
  .charging .event, .charging .level { top: 30px; }
  .charging .stamp { top: 91px; }

  .fade { position: absolute; left: 0; top: 990px; width: 675px; height: 111px;
    background: linear-gradient(to bottom, rgba(0,0,0,0), rgba(0,0,0,.95)); }

  .nav-bar { position: absolute; left: 0; bottom: 0; width: 675px; height: 99px; background: var(--nav-bg); }
  .nav-bar svg { position: absolute; top: 30px; }
</style>
</head>
<body>
  <header class="status-bar">
    <div class="status-icons">
      <svg width="32" height="24" viewBox="0 0 32 24" aria-hidden="true"><path d="M16 22 L1 7 Q16 -4 31 7 Z" fill="#fff"/></svg>
      <svg width="24" height="24" viewBox="0 0 24 24" aria-hidden="true"><path d="M2 22 L22 2 L22 22 Z" fill="#fff"/></svg>
      <svg width="16" height="26" viewBox="0 0 16 26" aria-hidden="true"><rect x="5" y="0" width="6" height="3" fill="#fff"/><rect x="0" y="3" width="16" height="23" fill="#fff"/></svg>
      <span class="status-time">12:06</span>
    </div>
  </header>

  <div class="app-bar">
    <div class="app-mark"></div>
    <h1 class="app-title">Velmora Power Saver</h1>
  </div>

  <nav class="tabs">
    <span class="tab tab-history">HISTORY</span>
    <span class="tab tab-current">CURRENT</span>
    <div class="tab-indicator"></div>
  </nav>

  <div class="log-count"><strong>336</strong> LOG ITEMS</div>

  <main class="log-list">
    <article class="log-card unplugged" style="top:324px">
      <svg class="edge" viewBox="0 0 20 160" preserveAspectRatio="none" aria-hidden="true"><path d="M0 0 H12 L20 80 L12 160 H0 Z" fill="currentColor"/></svg>
      <span class="event">UNPLUGGED</span><span class="level">100%</span>
      <span class="duration">After 0,8 hours plugged in</span>
      <span class="stamp date">24/09/2014</span><span class="stamp time">23:04</span><span class="stamp reading">39.5°C / 4.167V</span>
    </article>

    <article class="log-card charging" style="top:489px">
      <svg class="edge" viewBox="0 0 20 160" preserveAspectRatio="none" aria-hidden="true"><path d="M0 0 H12 L20 80 L12 160 H0 Z" fill="currentColor"/></svg>
      <span class="event">CHARGING (USB)</span><span class="level">100%</span>
      <span class="stamp date">24/09/2014</span><span class="stamp time">23:04</span><span class="stamp reading">34.9°C / 4.329V</span>
    </article>

    <article class="log-card unplugged" style="top:654px">
      <svg class="edge" viewBox="0 0 20 160" preserveAspectRatio="none" aria-hidden="true"><path d="M0 0 H12 L20 80 L12 160 H0 Z" fill="currentColor"/></svg>
      <span class="event">UNPLUGGED</span><span class="level">100%</span>
      <span class="duration">After 2,0 hours plugged in</span>
      <span class="stamp date">24/09/2014</span><span class="stamp time">22:11</span><span class="stamp reading">37.5°C / 4.21V</span>
    </article>

    <article class="log-card charging" style="top:819px">
      <svg class="edge" viewBox="0 0 20 160" preserveAspectRatio="none" aria-hidden="true"><path d="M0 0 H12 L20 80 L12 160 H0 Z" fill="currentColor"/></svg>
      <span class="event">CHARGING (USB)</span><span class="level">100%</span>
      <span class="stamp date">24/09/2014</span><span class="stamp time">20:58</span><span class="stamp reading">30.2°C / 4.33V</span>
    </article>

    <article class="log-card charging" style="top:986px">
      <svg class="edge" viewBox="0 0 20 160" preserveAspectRatio="none" aria-hidden="true"><path d="M0 0 H12 L20 80 L12 160 H0 Z" fill="currentColor"/></svg>
      <span class="event">CHARGING (USB)</span><span class="level">100%</span>
      <span class="stamp date">24/09/2014</span><span class="stamp time">20:58</span><span class="stamp reading">30.2°C / 4.33V</span>
    </article>
  </main>

  <div class="fade"></div>

  <footer class="nav-bar">
    <svg style="left:116px" width="64" height="40" viewBox="0 0 64 40" aria-label="Back"><path d="M14 6 L4 14 L14 22 M4 14 H46 Q60 14 60 24 Q60 34 46 34 H26" fill="none" stroke="#fff" stroke-width="3"/></svg>
    <svg style="left:301px" width="72" height="40" viewBox="0 0 72 40" aria-label="Home"><path d="M3 36 V16 L36 3 L69 16 V36 Z" fill="none" stroke="#fff" stroke-width="3"/></svg>
    <svg style="left:494px" width="66" height="40" viewBox="0 0 66 40" aria-label="Recent apps"><rect x="3" y="14" width="50" height="24" fill="none" stroke="#fff" stroke-width="3"/><path d="M13 8 H62 V30" fill="none" stroke="#fff" stroke-width="3"/></svg>
  </footer>
</body>
</html>
```